Lucky Harbour Fun Casino Entertainment

Looking to update my business card and make it look more modern, stand out and eye catching.
We are are fun casino business in Australia (primarily Sydney). Blackjack and Roulette are our most popular games although we have pretty much every game available for hire that you would find in a real casino. The final design would need to be sleek and appeal to the more upmarket corporate sector.
We mainly cater for Corporate Events, Private Parties, Fundraising Events, Team Building, Poker Tournaments
I think I'd prefer the colour Black.

Target Market(s)

High-end Corporate

Industry/Entity Type

Events

Contact Information for Business Card

Rob Kendall
Director
1300 482 617
0433 728 591
info@luckyharbour.com.au
www.luckyharbour.com.au
Facebook & Instagram @luckyharbourevents (proper social icons preferred)

Colors
000000
0255a3

Requirements
Must have
• Front side:
• Logo
• Contact details
• 'Australia's #1 Fun Casino Specialists'
• Back:
• Logo
Nice to have
• Back:
• Corporate Events
• Private Parties
• Poker Tournaments
• Fundraising
• Props & Theming
• Photo Booth
• Horse Racing Events
• The Vegas Sign attached, maybe on the back of the card in the background...?

```html
<!DOCTYPE html>
<html lang="en">
<head>
<meta charset="utf-8">
<title>Lucky Harbour Business Card</title>
<link href="https://fonts.googleapis.com/css2?family=Open+Sans:wght@400;600;700&display=swap" rel="stylesheet">
<style>
  :root {
    --page: #2a2a2a;
    --card: #1c1c1c;
    --accent: #f7a600;
    --text: #d9d9d9;
    --muted: #a8a8a8;
    --rule: #555555;
    --social: #0255a3;
  }
  * { margin: 0; padding: 0; box-sizing: border-box; }
  html, body { width: 1200px; height: 896px; overflow: hidden; }
  body {
    background: var(--page);
    font-family: "Open Sans", sans-serif;
    display: flex;
    flex-direction: column;
    align-items: center;
    justify-content: center;
    gap: 56px;
  }
  .card {
    width: 620px;
    height: 378px;
    background: var(--card);
    position: relative;
    box-shadow: 0 12px 30px rgba(0,0,0,0.45);
  }
  .brand {
    display: flex;
    align-items: center;
    gap: 12px;
  }
  .brand-dot {
    width: 34px; height: 34px;
    border-radius: 50%;
    background: var(--accent);
    flex: none;
  }
  .brand-name {
    color: var(--accent);
    font-weight: 700;
    font-size: 30px;
    letter-spacing: 1px;
    line-height: 1;
  }
  /* front */
  .card-front .brand { position: absolute; left: 44px; top: 70px; }
  .contact {
    position: absolute;
    left: 300px;
    top: 150px;
  }
  .person-name {
    color: var(--accent);
    font-weight: 700;
    font-size: 26px;
    letter-spacing: 1px;
    line-height: 1;
  }
  .person-role {
    color: var(--muted);
    font-size: 17px;
    margin: 4px 0 18px;
  }
  .contact-list { list-style: none; }
  .contact-list li {
    display: flex;
    align-items: center;
    gap: 9px;
    color: var(--text);
    font-size: 17px;
    line-height: 26px;
    letter-spacing: 0.5px;
  }
  .contact-icon {
    width: 17px; height: 17px;
    border-radius: 50%;
    background: var(--accent);
    display: flex;
    align-items: center;
    justify-content: center;
    flex: none;
  }
  /* back */
  .card-back {
    display: flex;
    flex-direction: column;
    align-items: center;
    justify-content: center;
  }
  .card-back .brand-name { font-size: 38px; }
  .card-back .brand-dot { width: 42px; height: 42px; }
  .tagline {
    color: var(--accent);
    font-weight: 600;
    font-size: 17px;
    letter-spacing: 1px;
    margin-top: 34px;
    padding-bottom: 12px;
    border-bottom: 1px solid var(--rule);
    width: 400px;
    text-align: center;
  }
  .social {
    display: flex;
    align-items: center;
    gap: 6px;
    margin-top: 12px;
    color: var(--text);
    font-size: 16px;
  }
  .social-dot {
    width: 20px; height: 20px;
    border-radius: 50%;
    background: var(--social);
  }
</style>
</head>
<body>

<section class="card card-front" aria-label="Business card front">
  <div class="brand">
    <span class="brand-dot"></span>
    <span class="brand-name">LUCKY HARBOUR</span>
  </div>
  <div class="contact">
    <p class="person-name">ROB KENDALL</p>
    <p class="person-role">Director</p>
    <ul class="contact-list">
      <li>
        <span class="contact-icon">
          <svg width="11" height="11" viewBox="0 0 24 24"><path fill="#1c1c1c" d="M6.6 10.8a15 15 0 0 0 6.6 6.6l2.2-2.2c.3-.3.7-.4 1-.2 1.1.4 2.3.6 3.6.6.6 0 1 .4 1 1V20c0 .6-.4 1-1 1A17 17 0 0 1 3 4c0-.6.4-1 1-1h3.5c.6 0 1 .4 1 1 0 1.3.2 2.5.6 3.6.1.3 0 .7-.2 1z"/></svg>
        </span>1300 482 617
      </li>
      <li>
        <span class="contact-icon">
          <svg width="10" height="10" viewBox="0 0 24 24"><rect x="6" y="2" width="12" height="20" rx="2" fill="#1c1c1c"/><rect x="8" y="5" width="8" height="11" fill="#f7a600"/></svg>
        </span>0433 728 591
      </li>
      <li>
        <span class="contact-icon">
          <svg width="11" height="11" viewBox="0 0 24 24"><rect x="3" y="5" width="18" height="14" rx="1" fill="#1c1c1c"/><path d="M3 6l9 7 9-7" stroke="#f7a600" stroke-width="2" fill="none"/></svg>
        </span>info@luckyharbour.com.au
      </li>
      <li>
        <span class="contact-icon">
          <svg width="11" height="11" viewBox="0 0 24 24"><circle cx="12" cy="12" r="9" fill="none" stroke="#1c1c1c" stroke-width="2.5"/><path d="M3 12h18M12 3c3 3 3 15 0 18M12 3c-3 3-3 15 0 18" stroke="#1c1c1c" stroke-width="2" fill="none"/></svg>
        </span>www.luckyharbour.com.au
      </li>
    </ul>
  </div>
</section>

<section class="card card-back" aria-label="Business card back">
  <div class="brand">
    <span class="brand-dot"></span>
    <span class="brand-name">LUCKY HARBOUR</span>
  </div>
  <p class="tagline">AUSTRALIA'S #1 FUN CASINO SPECIALISTS</p>
  <div class="social">
    <span class="social-dot"></span>
    <span class="social-dot"></span>
    <span class="social-handle">@luckyharbourevents</span>
  </div>
</section>

</body>
</html>
```